New, modern business card for growing audiology practice

We need a new business card for our audiology practice. Our logo and website have recently changed (more modern) and we want our business cards to reflect this change.
We conduct hearing tests, perform earwax removals, and fit & dispense hearing aids to our patients. We are a family owned practice in which the owner is the one who works directly with the patient. I have attached logos in various formats to use, as well as two ideas I found on this website; as well as a scanned copy of our current logo. Good luck!

Industry/Entity Type

Business

Contact Information for Business Card

Company name: Tolvera Hearing Center
Provider name: Peter Wolstenby, Au.D. F/NSB
Phone number: (440) 683-5127
Address: 837 W. Lindell Ave. Marlow Creek, OH 44091
email: tolverahearing@postvane.com
website: tolverahearing.com

Colors
000000
aaaaaa
dbdbdb
cacaca
9bcb3c
afd23c
cadf82
b1b1b1

Requirements
Must have
• My card must include information in the "details" section. In the attached images, I found a few that I liked and I would like to model after - "brisky bouncin'" and "Sound Method Center".
• Must be horizontal.
• Must include logos provided. I uploaded them in various file formats and various ways.
• Must match logo font, if possible, if not, please get as close as you can.
Nice to have
• I really like the idea of having a color on one side with just the logo and company name and the contact information and provider name on the other side. I also really like the idea of having the main color dominating on the logo/company side with accent of that same color on the contact side of the card.
Should not have
• Must not be vertical.

```html
<!DOCTYPE html>
<html lang="en">
<head>
<meta charset="utf-8">
<title>Tolvera Hearing Center – Business Card</title>
<link rel="stylesheet" href="https://fonts.googleapis.com/css2?family=Roboto:wght@400;500;700&display=swap">
<style>
  :root {
    --backdrop: #2c2c2c;
    --paper: #f1f1f1;
    --brand-green: #76a23b;
    --ink: #111111;
    --ink-soft: #555555;
    --white: #ffffff;
    --rule: #333333;
  }
  * { box-sizing: border-box; margin: 0; padding: 0; }
  html, body {
    width: 1200px; height: 960px; overflow: hidden;
    background: var(--backdrop);
    font-family: "Roboto", Arial, sans-serif;
  }
  .card {
    position: absolute;
    left: 320px;
    width: 600px; height: 342px;
    border-radius: 16px;
    overflow: hidden;
  }
  /* Logo side */
  .card--brand { top: 100px; background: var(--paper); }
  .brand-lockup {
    position: absolute; left: 97px; top: 166px; width: 413px;
    text-align: center;
  }
  .brand-name {
    font-weight: 400; font-size: 30px; letter-spacing: 1px;
    color: var(--ink); text-transform: uppercase; line-height: 1;
    padding-bottom: 5px; border-bottom: 1.5px solid var(--rule);
    white-space: nowrap;
  }
  .brand-url {
    margin-top: 7px; font-size: 14px; letter-spacing: 6.2px;
    color: var(--ink-soft); white-space: nowrap;
  }
  /* Contact side */
  .card--contact { top: 493px; background: var(--brand-green); }
  .contact-sweep { position: absolute; inset: 0; }
  .contact-brand {
    position: absolute; left: 36px; top: 44px;
    font-size: 21px; font-weight: 400; color: var(--ink);
    text-transform: uppercase; white-space: nowrap;
  }
  .provider { position: absolute; left: 35px; top: 150px; color: var(--white); }
  .provider-name { font-size: 21px; font-weight: 700; text-transform: uppercase; line-height: 28px; }
  .provider-title { font-size: 15px; font-weight: 500; margin-top: 0; }
  .address { margin-top: 13px; font-size: 14px; line-height: 18px; }
  .contact-list { list-style: none; margin-top: 10px; font-size: 14px; line-height: 19.5px; }
  .contact-list li { display: flex; align-items: center; gap: 9px; white-space: nowrap; }
  .contact-list svg { width: 14px; height: 14px; fill: var(--white); flex: none; }
</style>
</head>
<body>

<section class="card card--brand" aria-label="Business card, logo side">
  <div class="brand-lockup">
    <h1 class="brand-name">Tolvera Hearing Center</h1>
    <p class="brand-url">www.tolverahearing.com</p>
  </div>
</section>

<section class="card card--contact" aria-label="Business card, contact side">
  <svg class="contact-sweep" viewBox="0 0 600 342" aria-hidden="true">
    <path d="M445 0 C380 40 342 110 350 180 C358 250 410 290 420 342 L600 342 L600 0 Z" fill="var(--paper)"/>
  </svg>
  <p class="contact-brand">Tolvera Hearing Center</p>

  <div class="provider">
    <h2 class="provider-name">Peter Wolstenby</h2>
    <p class="provider-title">AU.D. F/NSB</p>
    <p class="address">837 W. Lindell Ave.<br>Marlow Creek, OH 44091</p>
    <ul class="contact-list">
      <li>
        <svg viewBox="0 0 24 24" aria-hidden="true"><path d="M6.6 10.8a15.1 15.1 0 0 0 6.6 6.6l2.2-2.2c.3-.3.7-.4 1-.2 1.1.4 2.3.6 3.6.6.6 0 1 .4 1 1V20c0 .6-.4 1-1 1A17 17 0 0 1 3 4c0-.6.4-1 1-1h3.5c.6 0 1 .4 1 1 0 1.3.2 2.5.6 3.6.1.3 0 .7-.2 1z"/></svg>
        (440) 683-5127
      </li>
      <li>
        <svg viewBox="0 0 24 24" aria-hidden="true"><path d="M2 5h20v14H2z"/><path d="M2 6l10 7 10-7v-1H2z" fill="var(--brand-green)"/></svg>
        tolverahearing@postvane.com
      </li>
      <li>
        <svg viewBox="0 0 24 24" aria-hidden="true"><circle cx="12" cy="12" r="10"/><path d="M7 7c2 0 3 1 3 3s2 2 2 4-1 3 0 5M15 4c-1 2 0 3 2 4s3 2 3 3" stroke="var(--brand-green)" stroke-width="2" fill="none"/></svg>
        tolverahearing.com
      </li>
    </ul>
  </div>
</section>

</body>
</html>
```